Indy Film Production Company/Studio

We need a business card designed from an existing logo. We are a digital studio/production company that caters to creating genre entertainment, like Action, Horror, and martial arts. The card along with the logo will be used to Brand the company from letter heads to banners. The design will also be used for postcards and Brochures. It should be professional and masculine.
Updates

Thank you to all the designers who have participated. I'm narrowing down who it will be. Thank you again.

Target Market(s)

Investors, Networks, Producers, and actors

Industry/Entity Type

Film Production

Contact Information for Business Card

Teodoro Valbuena
Producer/Writer/Director
www.kestrelpicturehouse.example

Requirements
Must have
• Website address, Facebook icon and Twitter icon possibly in the back of the card.
Nice to have
• Logline of Company: Follow The Action.

```html
<!DOCTYPE html>
<html lang="en">
<head>
<meta charset="utf-8">
<title>Kestrel Picture House – Business Card</title>
<link href="https://fonts.googleapis.com/css2?family=Open+Sans:wght@400;600;800&display=swap" rel="stylesheet">
<style>
  :root {
    --bg: #2e2a28;
    --card: #0d0d0d;
    --red: #e0252b;
    --white: #f2f2f2;
    --grey: #8a8a8a;
    --divider: #4a4a4a;
  }
  * { box-sizing: border-box; margin: 0; padding: 0; }
  html, body { width: 1200px; height: 814px; overflow: hidden; }
  body {
    background: var(--bg);
    font-family: "Open Sans", Arial, sans-serif;
    position: relative;
  }
  .card {
    position: absolute;
    top: 253px;
    width: 540px;
    height: 308px;
    background: var(--card);
    box-shadow: 0 10px 30px rgba(0,0,0,.45);
  }
  .card--front { left: 45px; }
  .card--back { left: 615px; }

  /* front */
  .front-brand {
    position: absolute;
    left: 34px; top: 0; bottom: 0;
    width: 200px;
    display: flex; align-items: center;
  }
  .brand-name {
    color: var(--red);
    font-weight: 800;
    font-size: 30px;
    line-height: 1.05;
    text-transform: uppercase;
  }
  .front-divider {
    position: absolute;
    left: 262px; top: 60px;
    width: 1px; height: 188px;
    background: var(--divider);
  }
  .front-details {
    position: absolute;
    left: 284px; top: 74px;
    color: var(--white);
  }
  .person-name {
    color: var(--red);
    font-size: 18px;
    font-weight: 600;
  }
  .person-role {
    font-size: 13px;
    margin-top: 2px;
    margin-bottom: 18px;
  }
  .contact-list { list-style: none; }
  .contact-item {
    display: flex; align-items: center;
    font-size: 12px;
    margin-bottom: 7px;
  }
  .contact-icon { width: 13px; height: 13px; margin-right: 9px; flex: none; }

  /* back */
  .social-links {
    position: absolute;
    right: 16px; top: 14px;
    display: flex; gap: 3px;
  }
  .social-square { width: 14px; height: 14px; background: var(--red); }
  .back-brand {
    position: absolute;
    left: 0; right: 0; top: 96px;
    text-align: center;
  }
  .back-brand .brand-name {
    color: var(--white);
    font-size: 40px;
  }
  .back-website {
    position: absolute;
    left: 0; right: 0; top: 212px;
    text-align: center;
    color: var(--white);
    font-size: 12px;
    letter-spacing: .5px;
  }
</style>
</head>
<body>
  <section class="card card--front" aria-label="Business card front">
    <div class="front-brand">
      <p class="brand-name">Kestrel<br>Picture House</p>
    </div>
    <div class="front-divider"></div>
    <div class="front-details">
      <p class="person-name">Teodoro Valbuena</p>
      <p class="person-role">Producer/Writer/Director</p>
      <ul class="contact-list">
        <li class="contact-item">
          <svg class="contact-icon" viewBox="0 0 16 16"><path fill="#e0252b" d="M3.6 1.2l2.3 2.6-1.4 1.8c.9 2 2.6 3.7 4.6 4.6l1.8-1.4 2.6 2.3-1.2 2.3C7 13 3 9 1.3 2.4z"/></svg>
          555 016 9041
        </li>
        <li class="contact-item">
          <svg class="contact-icon" viewBox="0 0 16 16"><rect x="1" y="3" width="14" height="10" fill="#e0252b"/><path d="M1 3l7 6 7-6" fill="none" stroke="#0d0d0d" stroke-width="1.4"/></svg>
          name@kestrelpicturehouse.example
        </li>
        <li class="contact-item">
          <svg class="contact-icon" viewBox="0 0 16 16"><circle cx="8" cy="8" r="7" fill="#e0252b"/><path d="M1 8h14M8 1c-3 3.5-3 10.5 0 14M8 1c3 3.5 3 10.5 0 14" fill="none" stroke="#0d0d0d" stroke-width="1"/></svg>
          www.kestrelpicturehouse.example
        </li>
      </ul>
    </div>
  </section>

  <section class="card card--back" aria-label="Business card back">
    <div class="social-links" aria-label="Social network links">
      <span class="social-square"></span>
      <span class="social-square"></span>
    </div>
    <div class="back-brand">
      <p class="brand-name">Kestrel<br>Picture House</p>
    </div>
    <p class="back-website">www.kestrelpicturehouse.example</p>
  </section>
</body>
</html>
```